Box for a Bold Bathroom - stylish minimalist package for a modern upscale brand

We need an adaptable package design using a color label on a brown box, or just a brown box with 2 or 3 color printing. The best design would be one that is adaptable for either use.

Our first products launching under this brand will be a series of medicine cabinets and mirrors, and our cartons can vary in size from 500x100x600 mm to 1200x300x1000 mm

About us: we produce a variety of bathroom fixtures including medicine cabinets, mirrors, vanities, etc. You've likely seen our products - we do manufacturing for Brantley, Marlowe, Thistle Cove, Dunmore & Pike, and others.

A version of our logo is attached for reference; we use it in a variety of color mixes depending on application. Vector available if needed or can be used FPO and our team will replace.

These are our colors, please take note and ignore the 'color' field:

Light Blue: C:66%/M:6%/Y:22%/K:0%; H:189° S:65% B:78%
Light Grey: C:35%/M:26%/Y:24%/K:0%; H:213° S:5% B:70%
Dark Blue: C:90%/M:50%/Y:44%/K:20%; H:189° S:82% B:43%
Dark Grey: C:70%/M:60%/Y:54%/K:38%; H:213° S:11% B:30%

Reason: Some revisions still outstanding before we can make selection, and some submissions we have agreed to wait for. Please submit all work ASAP so our team can provide feedback to you. Thanks!

Target Market(s)

DIY'ers; home renovators

Industry/Entity Type

Home Improvement

Font styles to use
Sans Serif

Requirements
Must have
• 1. Brand logo w/ logotype
• 2. Brand name without logo (can be on shipping mark side)
• 3. Multi-lingual En/Fr/Es (you do not need to include multi-lingual content but must allow space for our own translations if you do not)
• 4. Shipping/Handling Glyphs on 5 sides (all but bottom)
• i.e. fragile, this way up, team lift or mech lift, clamp or no clamp, max-stack
• 5. Two sides should include a marked 4" x 4" area for affixing labels (e.g. UPC, SSCC, etc.) ideally with a dotted line or corner marks or similar.
• 6. Shipping mark details or space for them (should be on the smallest side, only needed on one but can be on both) [see example file of shipping mark informations]
Nice to have
• Design that can be used either with color label on brown box, or brown box only.
• If designing for color label; please see the sample images included. Lifestyle should be prominent, the inside photo being smaller to help show interior features. These photos are obviously not useful for brown-box design.

```html
<!DOCTYPE html>
<html lang="en">
<head>
<meta charset="utf-8">
<title>Clearform Carton Dieline</title>
<link href="https://fonts.googleapis.com/css2?family=Montserrat:wght@500;600&family=Oswald:wght@400;500&display=swap" rel="stylesheet">
<style>
  :root {
    --bg: #e9ecee;
    --kraft: #bb9470;
    --kraft-light: #bf9b79;
    --crease: #8d6d52;
    --dark-blue: #1a5d6d;
    --light-blue: #2fc3d4;
    --dark-grey: #3f444d;
    --light-grey: #aeb1b6;
    --white: #ffffff;
  }
  html, body {
    margin: 0;
    width: 1200px;
    height: 1200px;
    overflow: hidden;
    background: var(--bg);
  }
  .dieline { display: block; width: 1200px; height: 1200px; }
  .panel { fill: var(--kraft); stroke: var(--crease); stroke-width: 0.8; }
  .flap { fill: var(--kraft-light); stroke: var(--crease); stroke-width: 0.8; }
  .rule { stroke: var(--dark-blue); stroke-width: 3; }
  .band { fill: var(--dark-blue); }
  .brand { font-family: "Montserrat", sans-serif; font-weight: 500; fill: var(--dark-grey); letter-spacing: 0.08em; }
  .brand-dot { fill: var(--light-blue); }
  .tagline { font-family: "Montserrat", sans-serif; font-weight: 600; font-style: italic; fill: var(--light-blue); font-size: 15px; letter-spacing: 0.04em; }
  .ship-mark { font-family: "Oswald", sans-serif; font-weight: 400; fill: var(--light-blue); font-size: 9.5px; }
  .label-zone { fill: var(--white); stroke: var(--dark-grey); stroke-width: 1.2; stroke-dasharray: 2 2; }
  .glyph-box { fill: none; stroke: var(--dark-grey); stroke-width: 1.2; }
  .glyph { fill: var(--dark-grey); stroke: none; }
  .glyph-line { fill: none; stroke: var(--dark-grey); stroke-width: 2; }
  .glyph-num { font-family: "Oswald", sans-serif; font-weight: 500; fill: var(--dark-grey); font-size: 16px; }
  .photo-curve { fill: none; stroke: var(--dark-blue); stroke-width: 9; }
</style>
</head>
<body>
<svg class="dieline" viewBox="0 0 1500 1500" xmlns="http://www.w3.org/2000/svg">
  <defs>
    <linearGradient id="lifestyle-tone" x1="0" y1="0" x2="1" y2="1">
      <stop offset="0" stop-color="#f4f7f9"/>
      <stop offset="0.55" stop-color="#c9dbe3"/>
      <stop offset="1" stop-color="#6f93a4"/>
    </linearGradient>
    <linearGradient id="interior-tone" x1="0" y1="0" x2="0" y2="1">
      <stop offset="0" stop-color="#f6f7f8"/>
      <stop offset="0.6" stop-color="#cfd3d7"/>
      <stop offset="1" stop-color="#b5bac0"/>
    </linearGradient>

    <g id="handling-glyphs">
      <rect class="glyph-box" x="0" y="0" width="28" height="28"/>
      <path class="glyph-line" d="M9 22 V7 M5 11 L9 6 L13 11 M19 22 V7 M15 11 L19 6 L23 11 M5 24 H23"/>
      <rect class="glyph-box" x="32" y="0" width="28" height="28"/>
      <path class="glyph-line" d="M36 8 Q40 20 46 22 Q52 20 56 8 M42 12 L46 16 L50 12"/>
      <rect class="glyph-box" x="64" y="0" width="28" height="28"/>
      <path class="glyph" d="M70 5 H86 Q86 16 79.5 17 V22 H84 V24 H72 V22 H76.5 V17 Q70 16 70 5 Z"/>
      <rect class="glyph-box" x="96" y="0" width="28" height="28"/>
      <path class="glyph-line" d="M102 8 H118 V20 H102 Z M102 8 L118 20 M118 8 L102 20"/>
      <rect class="glyph-box" x="128" y="0" width="28" height="28"/>
      <text class="glyph-num" x="142" y="20" text-anchor="middle">10</text>
      <path class="glyph-line" d="M132 24 H152"/>
    </g>
  </defs>

  <!-- top closure flaps -->
  <path class="flap" d="M341 190 L521 186 V375 H341 Z"/>
  <path class="flap" d="M978 186 L1159 190 V375 H978 Z"/>
  <path class="panel" d="M521 375 V187 H523 V172 Q523 152 545 152 H953 Q975 152 975 172 V187 H978 V375 Z"/>
  <rect x="680" y="181" width="140" height="4" rx="2" fill="var(--white)"/>
  <rect class="band" x="521" y="263" width="457" height="35"/>
  <g transform="rotate(180 749.5 280.5)">
    <text class="tagline" x="749.5" y="286" text-anchor="middle">STYLISH BATHROOM FIXTURES</text>
  </g>
  <g transform="rotate(180 875 342)">
    <circle class="brand-dot" cx="802" cy="342" r="8"/>
    <text class="brand" x="818" y="347" font-size="13">CLEARFORM</text>
  </g>

  <!-- main wrap: glue flap, sides, front -->
  <path class="panel" d="M145 378 H333 V773 H145 V675 Q135 675 135 660 V490 Q135 475 145 475 Z"/>
  <rect class="panel" x="333" y="378" width="188" height="395"/>
  <rect class="panel" x="521" y="378" width="457" height="395"/>
  <rect class="panel" x="978" y="378" width="189" height="395"/>
  <path class="panel" d="M1167 378 H1355 V475 Q1365 475 1365 490 V660 Q1365 675 1355 675 V773 H1167 Z"/>
  <line class="rule" x1="145" y1="377" x2="1355" y2="377"/>
  <line class="rule" x1="145" y1="774" x2="1355" y2="774"/>

  <!-- left side: shipping mark -->
  <circle class="brand-dot" cx="364" cy="416" r="8"/>
  <text class="brand" x="380" y="421" font-size="13">CLEARFORM</text>
  <rect class="band" x="360" y="602" width="178" height="150" rx="2"/>
  <g class="ship-mark">
    <text x="377" y="628">LOT#: 12340506</text>
    <text x="377" y="642">ITEM #: XXX00000A</text>
    <text x="377" y="656">DIM: 109.2 X 45.1 X 95.9 CM</text>
    <text x="395" y="670">(43" X 17 " X 37 ")</text>
    <text x="377" y="684">NW / PN:        KG (        LB)</text>
    <text x="377" y="698">GW / PB:        KG (        LB)</text>
    <text x="377" y="712">CUBE: 99.449 M  (999.9FT )</text>
    <text x="377" y="726">QTY: 1</text>
    <text x="377" y="740">CASE</text>
  </g>

  <!-- front: lifestyle photo -->
  <path role="img" aria-label="Lifestyle photo of a modern bathroom vanity with vessel sink, faucet and backlit mirror" fill="url(#lifestyle-tone)" d="M521 378 H978 V652 C800 652 600 560 521 378 Z"/>
  <path class="photo-curve" d="M521 378 C600 560 800 652 978 652"/>
  <circle class="brand-dot" cx="618" cy="412" r="10"/>
  <text class="brand" x="620" y="440" font-size="12" text-anchor="middle">CLEARFORM</text>
  <use href="#handling-glyphs" x="563" y="720"/>
  <rect class="label-zone" x="916" y="716" width="42" height="42"/>

  <!-- right side: interior photo -->
  <path role="img" aria-label="Photo of an open mirrored medicine cabinet showing interior shelves" fill="url(#interior-tone)" d="M978 378 H1167 V664 C1090 664 1030 660 978 654 Z"/>
  <path class="photo-curve" d="M978 656 C1030 662 1090 668 1167 668" stroke-width="14"/>
  <circle class="brand-dot" cx="1006" cy="416" r="8"/>
  <text class="brand" x="1022" y="421" font-size="13">CLEARFORM</text>
  <use href="#handling-glyphs" x="993" y="720"/>

  <!-- lower closure flaps -->
  <path class="flap" d="M341 778 L521 776 V962 H341 Z"/>
  <rect class="panel" x="521" y="776" width="457" height="190"/>
  <path class="flap" d="M978 776 L1159 778 V962 H978 Z"/>
  <g transform="rotate(180 750 871)">
    <text class="brand" x="750" y="877" font-size="18" text-anchor="middle">CLEARFORM</text>
  </g>

  <!-- back panel with side dust flaps and tuck tab -->
  <path class="panel" d="M685 1333 H815 V1384 Q815 1398 800 1398 H700 Q685 1398 685 1384 Z"/>
  <path class="flap" d="M521 965 L400 995 Q355 1006 355 1050 V1290 Q355 1330 400 1340 L521 1365 Z"/>
  <path class="flap" d="M978 965 L1099 995 Q1144 1006 1144 1050 V1290 Q1144 1330 1099 1340 L978 1365 Z"/>
  <rect class="panel" x="521" y="965" width="457" height="400"/>
  <line class="rule" x1="521" y1="966" x2="978" y2="966"/>
  <rect class="label-zone" x="541" y="985" width="42" height="42"/>
  <g transform="rotate(180 874.5 1006)">
    <use href="#handling-glyphs" x="796" y="992"/>
  </g>
  <g transform="rotate(180 750 1175)">
    <text class="brand" x="750" y="1140" font-size="24" text-anchor="middle">CLEARFORM</text>
    <circle class="brand-dot" cx="750" cy="1200" r="22"/>
  </g>
</svg>
</body>
</html>
```